Plakat für Hausverwaltung
Zielgruppe
Hausverwaltung
(Verwaltung von Wohn- und Gewerbeimmobilien)
Aufgabenstellung
Es soll ein Werbeplakat werden, Die Inhalte der Dienstleistung und die Firmenfarben kann der Webseite entnommen werden.
Ein guter Werbespruch und ansprechendes Desing ohne viel Schrift.

```html
<!DOCTYPE html>
<html lang="de">
<head>
<meta charset="utf-8">
<title>RMK Hausverwaltung – Plakat</title>
<link rel="stylesheet" href="https://fonts.googleapis.com/css2?family=Lora:wght@500;700&family=Poppins:wght@500;600;700&display=swap">
<style>
  :root {
    --stage: #9c9c9c;
    --cream: #f7f2ea;
    --cream-warm: #efe4d3;
    --gold: #d9b765;
    --gold-soft: #ead9ae;
    --taupe: #8c8173;
    --taupe-light: #c3b6a4;
    --ink: #111111;
    --band: #050505;
    --white: #ffffff;
  }
  * { margin: 0; padding: 0; box-sizing: border-box; }
  html, body { width: 923px; height: 1200px; overflow: hidden; background: var(--stage); }
  .poster {
    position: absolute; left: 30px; top: 300px; width: 863px; height: 601px;
    overflow: hidden;
    background:
      radial-gradient(ellipse 300px 260px at 120px 40px, rgba(255,255,255,0.9), transparent 70%),
      linear-gradient(135deg, var(--cream) 0%, var(--cream-warm) 55%, var(--cream) 100%);
  }
  .gold-waves {
    position: absolute; left: 330px; top: -20px; width: 380px; height: 470px;
    background:
      radial-gradient(ellipse 70px 240px at 250px 140px, rgba(217,183,101,0.75), transparent 75%),
      radial-gradient(ellipse 200px 60px at 170px 270px, rgba(217,183,101,0.55), transparent 75%),
      radial-gradient(ellipse 150px 230px at 190px 200px, rgba(234,217,174,0.55), transparent 75%);
  }
  .dots-top {
    position: absolute; left: 660px; top: 0; width: 203px; height: 170px;
    background: radial-gradient(ellipse 200px 170px at 180px 40px, rgba(168,140,112,0.45), transparent 75%);
  }
  .dots-left {
    position: absolute; left: 10px; top: 175px; width: 190px; height: 190px;
    background: radial-gradient(ellipse 100px 100px at 100px 90px, rgba(170,160,150,0.35), transparent 75%);
  }
  .headline {
    position: absolute; left: 63px; top: 34px;
    font-family: "Lora", serif; font-weight: 700; font-size: 50.5px; line-height: 51px;
    color: var(--ink); letter-spacing: -0.3px;
  }
  .intro {
    position: absolute; left: 63px; top: 142px;
    font-family: "Poppins", sans-serif; font-weight: 500; font-size: 14.8px; line-height: 18px;
    color: var(--ink);
  }
  .team-photo {
    position: absolute; left: 0; top: 188px; width: 572px; height: 340px;
    background: linear-gradient(90deg, #e3d6c3 0%, #dccdb8 22%, #26304a 38%, #e9e6e0 44%, #25304a 56%, #5d6572 64%, #6f7680 78%, #596170 100%);
    -webkit-mask-image: linear-gradient(180deg, transparent 0%, rgba(0,0,0,0.5) 25%, #000 55%);
    mask-image: linear-gradient(180deg, transparent 0%, rgba(0,0,0,0.5) 25%, #000 55%);
  }
  .offers-title {
    position: absolute; left: 556px; top: 200px; width: 307px; height: 38px;
    background: var(--taupe); border-radius: 19px 0 0 19px;
    font-family: "Lora", serif; font-weight: 500; font-size: 25.5px; line-height: 38px;
    color: var(--white); padding-left: 28px;
  }
  .offers {
    position: absolute; left: 536px; top: 250px; width: 300px; list-style: none;
    text-align: center;
    font-family: "Poppins", sans-serif; font-weight: 600; font-size: 16.4px; line-height: 20px; color: var(--ink);
  }
  .offers li { height: 46px; display: flex; flex-direction: column; align-items: center; white-space: nowrap; }
  .offers svg { display: block; margin-bottom: 4px; }
  .divider { position: absolute; left: 577px; top: 417px; width: 218px; height: 1.5px; background: var(--taupe-light); }
  .brand {
    position: absolute; left: 561px; top: 448px; width: 280px; text-align: center;
    font-family: "Lora", serif; font-weight: 500; color: #333;
  }
  .brand-name { font-size: 22px; letter-spacing: 8px; line-height: 26px; }
  .brand-sub { font-size: 12px; line-height: 18px; white-space: nowrap; }
  .contact-band {
    position: absolute; left: 0; top: 527px; width: 863px; height: 55px; background: var(--band);
    display: flex; align-items: center; padding-left: 63px;
    font-family: "Poppins", sans-serif; font-weight: 600; font-size: 19.5px; color: var(--white);
  }
  .contact-item { display: flex; align-items: center; gap: 7px; }
  .contact-sep { width: 2px; height: 28px; background: var(--white); margin: 0 19px; }
  .contact-icon { width: 20px; height: 20px; border-radius: 50%; background: var(--taupe-light); display: flex; align-items: center; justify-content: center; }
</style>
</head>
<body>
<main class="poster">
  <div class="gold-waves" role="img" aria-label="Dekorative goldene Wellenlinien"></div>
  <div class="dots-top" role="img" aria-label="Dekoratives Punkteraster"></div>
  <div class="dots-left" role="img" aria-label="Dekoratives Punkteraster"></div>

  <h1 class="headline">RMK Haus- und<br>Immobilienverwaltungs GmbH</h1>
  <p class="intro">wir rund 1.400 Wohn- und Gewerbeeinheiten und sorgen für eine<br>reibungslose und zuverlässige Verwaltung Ihrer Immobilien.</p>

  <div class="team-photo" role="img" aria-label="Teamfoto: drei Mitarbeitende der Hausverwaltung in Business-Kleidung"></div>

  <div class="offers-title">Unsere Angebote</div>
  <ul class="offers">
    <li><svg width="15" height="15" viewBox="0 0 16 16"><circle cx="8" cy="8" r="8" fill="#8c8173"/><path d="M4.5 8.2l2.3 2.3 4.7-4.8" stroke="#fff" stroke-width="1.8" fill="none"/></svg>SONDEREIGENTUMVERWALTUNG</li>
    <li><svg width="15" height="15" viewBox="0 0 16 16"><circle cx="8" cy="8" r="8" fill="#8c8173"/><path d="M4.5 8.2l2.3 2.3 4.7-4.8" stroke="#fff" stroke-width="1.8" fill="none"/></svg>WOHNEIGENTUMSVERWALTUNG</li>
    <li><svg width="15" height="15" viewBox="0 0 16 16"><circle cx="8" cy="8" r="8" fill="#8c8173"/><path d="M4.5 8.2l2.3 2.3 4.7-4.8" stroke="#fff" stroke-width="1.8" fill="none"/></svg>MIETVERWALTUNG</li>
  </ul>
  <div class="divider"></div>

  <div class="brand">
    <div class="brand-name">RMK</div>
    <div class="brand-sub">RMK Haus- und Grundstücksverwaltungs GmbH</div>
  </div>

  <footer class="contact-band">
    <span class="contact-item">
      <span class="contact-icon"><svg width="11" height="11" viewBox="0 0 24 24"><path d="M6.6 10.8a15 15 0 006.6 6.6l2.2-2.2c.3-.3.7-.4 1-.2 1.1.4 2.3.6 3.6.6.6 0 1 .4 1 1V20c0 .6-.4 1-1 1A17 17 0 013 4c0-.6.4-1 1-1h3.5c.6 0 1 .4 1 1 0 1.3.2 2.5.6 3.6.1.3 0 .7-.2 1z" fill="#050505"/></svg></span>
      06421 938215
    </span>
    <span class="contact-sep"></span>
    <span class="contact-item">
      <span class="contact-icon"><svg width="11" height="11" viewBox="0 0 24 24"><rect x="3" y="5" width="18" height="14" rx="1" fill="none" stroke="#050505" stroke-width="2"/><path d="M3 6l9 7 9-7" fill="none" stroke="#050505" stroke-width="2"/></svg></span>
      info@rmk-lahntal.de
    </span>
    <span class="contact-sep"></span>
    <span class="contact-item">
      <span class="contact-icon"><svg width="12" height="12" viewBox="0 0 24 24" fill="none" stroke="#050505" stroke-width="2"><circle cx="12" cy="12" r="9"/><ellipse cx="12" cy="12" rx="4" ry="9"/><path d="M3 12h18"/></svg></span>
      www.rmk-lahntal.de
    </span>
  </footer>
</main>
</body>
</html>
```